Business Card Design

It's an investment advisory service for individuals with all there investment needs. Also financial consulting to businesses and governmental agencies on retirement plans etc. It's personalized not commoditized help. Should show strength, knowledge and money orientation.

Reason: Will be out of town setting up office.

Reason: waiting for the 2/3rds of group to vote

Reason: only half the votes are in, I'm calling and getting verbals, but at this time we are down to 2 designs.

Industry/Entity Type

Investment

Contact Information for Business Card

B. Rel K. Financial Consulting and Wealth Management, Berislav Mike Holcek, 5172 Pasadena Loma Verde, San Diego, CA 94417-6381, Registered Investment Advisor

Requirements
Nice to have
• Something money oriented

```html
<!DOCTYPE html>
<html lang="en">
<head>
<meta charset="utf-8">
<title>B. Rel K. Business Card</title>
<link href="https://fonts.googleapis.com/css2?family=Ubuntu:wght@400;500;700&display=swap" rel="stylesheet">
<style>
  :root {
    --page-bg: #ecebe7;
    --card-green: #1f6b2f;
    --brand-green: #25713a;
    --ink-dark: #3d3f3d;
    --ink-light: #ffffff;
    --photo-top: #f1f2f1;
    --photo-mid: #d9dbd8;
    --photo-bottom: #c4c7c3;
  }
  * { box-sizing: border-box; margin: 0; padding: 0; }
  html, body {
    width: 1200px;
    height: 1000px;
    overflow: hidden;
    background: var(--page-bg);
    font-family: "Ubuntu", Arial, sans-serif;
  }
  .canvas {
    position: relative;
    width: 1200px;
    height: 1000px;
  }
  .business-card {
    position: absolute;
    left: 150px;
    top: 238px;
    width: 900px;
    height: 524px;
    display: flex;
    box-shadow: 0 6px 22px rgba(0,0,0,0.18);
  }
  .brand-side {
    position: relative;
    width: 441px;
    height: 100%;
    background: linear-gradient(180deg, var(--photo-top) 0%, var(--photo-mid) 55%, var(--photo-bottom) 100%);
  }
  .brand-lockup {
    position: absolute;
    left: 0;
    top: 142px;
    width: 100%;
    display: flex;
    flex-direction: column;
    align-items: center;
  }
  .brand-name {
    display: flex;
    align-items: center;
    gap: 14px;
    height: 174px;
    color: var(--brand-green);
    font-weight: 700;
    font-size: 44px;
  }
  .brand-square {
    width: 26px;
    height: 26px;
    background: var(--brand-green);
  }
  .brand-tagline {
    margin-top: 30px;
    text-align: center;
    color: var(--ink-dark);
    font-weight: 400;
    font-size: 22px;
    line-height: 30px;
  }
  .contact-side {
    flex: 1;
    background: var(--card-green);
    color: var(--ink-light);
    padding: 148px 0 0 36px;
  }
  .person-name {
    font-weight: 500;
    font-size: 32px;
    line-height: 38px;
  }
  .person-credentials,
  .person-title {
    font-weight: 500;
    font-size: 20px;
    line-height: 28px;
  }
  .person-credentials sup { font-size: 12px; }
  .contact-list {
    list-style: none;
    margin-top: 18px;
    font-size: 23px;
    line-height: 36px;
  }
  .contact-list .email { margin-top: 6px; }
</style>
</head>
<body>
<main class="canvas">
  <article class="business-card">
    <section class="brand-side" role="img" aria-label="Faded photograph of bull and bear statues in front of a stock exchange building">
      <div class="brand-lockup">
        <div class="brand-name"><span class="brand-square"></span>B. Rel K.</div>
        <p class="brand-tagline">Financial Consulting<br>and Wealth Management</p>
      </div>
    </section>
    <section class="contact-side">
      <h1 class="person-name">Berislav "Mike" Holcek</h1>
      <p class="person-credentials">MBA, RP<sup>®</sup>, CRC<sup>®</sup></p>
      <p class="person-title">Registered Investment Advisor</p>
      <ul class="contact-list">
        <li class="phone">619-384-7150</li>
        <li class="phone">702-516-9283</li>
        <li class="email">mike.holcek@relkmail.com</li>
      </ul>
    </section>
  </article>
</main>
</body>
</html>
```